Specialised investor in e-mobility and energy wants business card design

We need a business card design that fits our existing corporate design. <The look and feel must be 'sharp'/'clean', dynamic, communicate momentum, professionalism etc (as one would imagine from a firm in the financial sector). We like the idea of a reverse-side of the card that includes the logo, and the name and contact details on the other. We expect the deliverable to be whatever format might be required to be able to get cards printed directly by a service such as kelmo press. Our website is www.zub.capital

```html
<!DOCTYPE html>
<html lang="en">
<head>
<meta charset="UTF-8">
<title>ZUB Capital – Business Card</title>
<link rel="stylesheet" href="https://fonts.googleapis.com/css2?family=Montserrat:wght@400;500;700&display=swap">
<style>
  :root {
    --page-bg: #1e1e1e;
    --card-green: #344f24;
    --accent-green: #7fb241;
    --text-white: #ffffff;
    --card-radius: 18px;
  }
  * { margin: 0; padding: 0; box-sizing: border-box; }
  html, body {
    width: 1200px;
    height: 1059px;
    overflow: hidden;
    background: var(--page-bg);
    font-family: "Montserrat", sans-serif;
    color: var(--text-white);
  }
  .canvas { position: relative; width: 1200px; height: 1059px; }
  .card {
    position: absolute;
    background: var(--card-green);
    border-radius: var(--card-radius);
  }
  .card--front { left: 257px; top: 89px; width: 687px; height: 390px; }
  .card--back  { left: 254px; top: 547px; width: 693px; height: 393px; }

  .wordmark {
    position: absolute;
    display: flex;
    align-items: center;
    gap: 0.25em;
    font-weight: 500;
    color: var(--text-white);
    white-space: nowrap;
    letter-spacing: 0.01em;
  }
  .wordmark__dot {
    width: 0.32em;
    height: 0.32em;
    border-radius: 50%;
    background: var(--accent-green);
    flex: none;
  }
  .card--front .wordmark { left: 41px; top: 170px; font-size: 38px; }
  .card--back .wordmark { left: 0; right: 0; top: 150px; justify-content: center; font-size: 76px; }

  .divider {
    position: absolute;
    left: 343px; top: 107px;
    width: 1px; height: 176px;
    background: var(--accent-green);
  }
  .details { position: absolute; left: 370px; top: 104px; }
  .details__name {
    font-weight: 700;
    font-size: 25px;
    line-height: 1.1;
    color: var(--accent-green);
    letter-spacing: 0.01em;
  }
  .details__title { font-size: 15.5px; line-height: 1.3; letter-spacing: 0.03em; }
  .details__address {
    margin-top: 10px;
    font-size: 15.5px;
    line-height: 22px;
    font-style: normal;
    letter-spacing: 0.03em;
  }
  .contact-list { list-style: none; margin-top: 7px; }
  .contact-list__item {
    display: flex;
    align-items: center;
    gap: 7px;
    font-size: 16px;
    height: 27.5px;
    letter-spacing: 0.03em;
  }
  .contact-list__icon { width: 11px; height: 11px; flex: none; fill: var(--accent-green); }
</style>
</head>
<body>
<main class="canvas">
  <section class="card card--front" aria-label="Business card front">
    <div class="wordmark"><span class="wordmark__dot"></span>ZUB Capital</div>
    <div class="divider"></div>
    <div class="details">
      <h1 class="details__name">Marten Olvey</h1>
      <p class="details__title">Director/Founder</p>
      <address class="details__address">1234 Street Name<br>Country Name AB 5748</address>
      <ul class="contact-list">
        <li class="contact-list__item">
          <svg class="contact-list__icon" viewBox="0 0 24 24" aria-hidden="true"><path d="M6.6 10.8a15.1 15.1 0 0 0 6.6 6.6l2.2-2.2a1 1 0 0 1 1-.25 11.4 11.4 0 0 0 3.6.6 1 1 0 0 1 1 1V20a1 1 0 0 1-1 1A17 17 0 0 1 3 4a1 1 0 0 1 1-1h3.5a1 1 0 0 1 1 1c0 1.25.2 2.45.6 3.6a1 1 0 0 1-.25 1z"/></svg>
          123-480-2917
        </li>
        <li class="contact-list__item">
          <svg class="contact-list__icon" viewBox="0 0 24 24" aria-hidden="true"><path d="M2 5h20v14H2z M2 5l10 8 10-8" fill="var(--accent-green)"/><path d="M3 6l9 7 9-7" fill="none" stroke="var(--card-green)" stroke-width="1.6"/></svg>
          info@zub.capital
        </li>
        <li class="contact-list__item">
          <svg class="contact-list__icon" viewBox="0 0 24 24" aria-hidden="true"><circle cx="12" cy="12" r="11"/><path d="M1 12h22M12 1c3 3 4.5 7 4.5 11S15 20 12 23M12 1C9 4 7.5 8 7.5 12S9 20 12 23" fill="none" stroke="var(--card-green)" stroke-width="1.5"/></svg>
          www.zub.capital
        </li>
      </ul>
    </div>
  </section>

  <section class="card card--back" aria-label="Business card back">
    <div class="wordmark"><span class="wordmark__dot"></span>ZUB Capital</div>
  </section>
</main>
</body>
</html>
```